Business Card for a New Zealand IT Startup

I need a business card for VELTA Holdings. We are a young startup based in New Zealand working in internet marketing and web development. The design should have some element connected to New Zealand, such as wave, koru or silver fern, just don't use a kiwi bird.

```html
<!DOCTYPE html>
<html lang="en">
<head>
<meta charset="utf-8">
<title>VELTA Holdings – Business Card</title>
<link rel="stylesheet" href="https://fonts.googleapis.com/css2?family=Source+Sans+3:wght@400;600;700&display=swap">
<style>
  :root {
    --page-bg: #e9e7e4;
    --card-bg: #f4f5f6;
    --card-edge: #d8dadd;
    --brand-blue: #1b6fa8;
    --brand-blue-deep: #165f92;
    --accent-orange: #e0622a;
    --text-dark: #333a40;
  }
  * { margin: 0; padding: 0; box-sizing: border-box; }
  html, body {
    width: 1200px;
    height: 1054px;
    overflow: hidden;
    background: var(--page-bg);
    font-family: "Source Sans 3", sans-serif;
  }
  .business-card {
    position: absolute;
    left: 100px;
    top: 225px;
    width: 1000px;
    height: 605px;
    background: var(--card-bg);
    border: 1px solid var(--card-edge);
    border-radius: 4px;
    overflow: hidden;
    box-shadow: 0 10px 30px rgba(0,0,0,0.12);
  }
  .brand-name {
    position: absolute;
    left: 44px;
    top: 56px;
    display: flex;
    align-items: center;
    gap: 14px;
    color: var(--brand-blue);
    font-weight: 700;
    font-size: 52px;
    line-height: 1;
    letter-spacing: 1px;
  }
  .brand-dot {
    width: 40px;
    height: 40px;
    border-radius: 50%;
    background: var(--brand-blue);
  }
  .wave-emblem {
    position: absolute;
    left: 531px;
    top: 34px;
    width: 537px;
    height: 537px;
    border-radius: 50%;
    background: radial-gradient(circle at 45% 55%, var(--brand-blue) 0%, var(--brand-blue-deep) 100%);
  }
  .person {
    position: absolute;
    left: 44px;
    top: 290px;
  }
  .person-name {
    color: var(--brand-blue);
    font-weight: 600;
    font-size: 38px;
    line-height: 1.1;
  }
  .person-title {
    color: var(--text-dark);
    font-size: 22px;
    margin-top: 4px;
  }
  .contact-list {
    position: absolute;
    left: 44px;
    top: 406px;
    list-style: none;
  }
  .contact-item {
    display: flex;
    align-items: center;
    gap: 20px;
    color: var(--text-dark);
    font-size: 23px;
    height: 35px;
  }
  .contact-icon {
    width: 20px;
    height: 20px;
    fill: var(--accent-orange);
    stroke: var(--accent-orange);
  }
  .address {
    position: absolute;
    left: 44px;
    top: 532px;
    color: var(--text-dark);
    font-size: 23px;
  }
</style>
</head>
<body>
  <main class="business-card">
    <div class="brand-name"><span>VELTA Holdings</span><span class="brand-dot"></span></div>

    <div class="wave-emblem" role="img" aria-label="Large New Zealand koru wave emblem in brand blue"></div>

    <section class="person">
      <h1 class="person-name">Aroha Millar</h1>
      <p class="person-title">Managing Director</p>
    </section>

    <ul class="contact-list">
      <li class="contact-item">
        <svg class="contact-icon" viewBox="0 0 20 20" aria-hidden="true">
          <path stroke="none" d="M2 6c0-2 3-3 8-3s8 1 8 3v2h-4V6.5c-1-.5-2.5-.7-4-.7s-3 .2-4 .7V8H2z"/>
          <path stroke="none" d="M4 10h12l1 7H3z"/>
        </svg>
        <span>021-555-0148</span>
      </li>
      <li class="contact-item">
        <svg class="contact-icon" viewBox="0 0 20 20" aria-hidden="true">
          <rect x="2" y="4" width="16" height="12" stroke="none"/>
          <path d="M2.5 4.5 10 11l7.5-6.5" fill="none" stroke="#f4f5f6" stroke-width="1.5"/>
        </svg>
        <span>hello@veltaholdings.com</span>
      </li>
      <li class="contact-item">
        <svg class="contact-icon" viewBox="0 0 20 20" aria-hidden="true">
          <circle cx="10" cy="10" r="8" stroke="none"/>
          <path d="M2 10h16M10 2c-3 3-3 13 0 16M10 2c3 3 3 13 0 16" fill="none" stroke="#f4f5f6" stroke-width="1.2"/>
        </svg>
        <span>www.veltaholdings.com</span>
      </li>
    </ul>

    <p class="address">18 Harbour Lane, Te Aro, Wellington, NZ 6011</p>
  </main>
</body>
</html>
```